Professional & attention grabbing.

A business card design, front and back. I already have a logo I will attach, but I am open to something new as well.
Things to include:
Name:
Title:
Phone:
Email:
Wanting something that is professional but attention grabbing.
Also we do a lot of work using drones on natural gas pipelines (leading the future)if you want to include any of that. I'm open to ideas.
Target Market(s)
Natural gas transmission industry / greenhouse gas mitigation industry
Industry/Entity Type
Business
Colors
Designer to choose colors to be used in the design.
Look and feel
Each slider illustrates characteristics of the customer's brand and the style your logo design should communicate.

```html
<!DOCTYPE html>
<html lang="en">
<head>
<meta charset="utf-8">
<title>Halvern Inspections – Business Card</title>
<link rel="stylesheet" href="https://fonts.googleapis.com/css2?family=Roboto+Condensed:wght@300;400;700&display=swap">
<style>
  :root {
    --page-bg: #2a2a2a;
    --card-white: #ffffff;
    --brand-red: #c4161c;
    --brand-red-dark: #9e1015;
    --sweep-grey: #4a4a4a;
    --logo-grey: #5a5a5a;
    --card-black: #1e1e1e;
    --card-black-light: #3a3a3a;
    --text-white: #ffffff;
    --text-muted: #cfcfcf;
  }
  * { margin: 0; padding: 0; box-sizing: border-box; }
  html, body {
    width: 1200px; height: 950px; overflow: hidden;
    background: var(--page-bg);
    font-family: "Roboto Condensed", "Arial Narrow", sans-serif;
  }
  .sheet {
    position: relative; width: 1200px; height: 950px;
    display: flex; flex-direction: column; align-items: center; justify-content: center; gap: 40px;
  }
  .card {
    position: relative; width: 700px; height: 400px; overflow: hidden;
    box-shadow: 0 10px 30px rgba(0,0,0,.45);
  }
  .card-front { background: var(--card-white); }
  .card-front .sweep { position: absolute; inset: 0; width: 100%; height: 100%; }

  .wordmark {
    display: flex; align-items: center; gap: 14px;
    font-weight: 700; text-transform: uppercase; white-space: nowrap;
  }
  .wordmark-square { width: 30px; height: 30px; background: var(--brand-red); flex: none; }
  .wordmark-text { display: flex; flex-direction: column; line-height: 1; }
  .wordmark-name { font-size: 46px; letter-spacing: 1px; }
  .wordmark-sub { font-size: 15px; letter-spacing: 3.2px; margin-top: 6px; }

  .card-front .wordmark {
    position: absolute; left: 48px; top: 168px;
    color: var(--logo-grey);
  }

  .contact {
    position: absolute; right: 40px; top: 62px; text-align: right; color: var(--text-white);
  }
  .contact-name { font-size: 28px; font-weight: 400; text-transform: uppercase; letter-spacing: .5px; }
  .contact-title { font-size: 20px; font-weight: 300; margin-bottom: 18px; }
  .contact-line {
    display: flex; justify-content: flex-end; align-items: center; gap: 10px;
    font-size: 17px; font-weight: 300; line-height: 28px;
  }
  .contact-icon { width: 16px; height: 16px; flex: none; }

  .card-back {
    background: linear-gradient(160deg, var(--card-black-light) 0%, var(--card-black) 55%, #141414 100%);
  }
  .card-back .wordmark {
    position: absolute; left: 50%; top: 50%; transform: translate(-50%, -50%);
    color: var(--text-white);
  }
  .card-back .wordmark-name { font-size: 60px; }
  .card-back .wordmark-sub { font-size: 19px; letter-spacing: 4.4px; margin-top: 8px; }
  .back-web {
    position: absolute; left: 40px; top: 50%;
    transform: translate(-50%, -50%) rotate(90deg);
    color: var(--text-muted); font-size: 13px; font-weight: 300; letter-spacing: 6px; white-space: nowrap;
  }
</style>
</head>
<body>
<main class="sheet">

  <section class="card card-front" aria-label="Card front">
    <svg class="sweep" viewBox="0 0 700 400" preserveAspectRatio="none" aria-hidden="true">
      <path d="M400 0 C500 120 250 250 300 400 L700 400 L700 0 Z" fill="var(--sweep-grey)"/>
      <path d="M430 0 C530 120 280 250 330 400 L700 400 L700 0 Z" fill="var(--brand-red)"/>
      <path d="M600 0 L700 0 L700 400 L480 400 C560 300 640 160 600 0 Z" fill="var(--brand-red-dark)" opacity=".25"/>
    </svg>

    <div class="wordmark">
      <span class="wordmark-square"></span>
      <span class="wordmark-text">
        <span class="wordmark-name">Halvern</span>
        <span class="wordmark-sub">Inspections</span>
      </span>
    </div>

    <div class="contact">
      <p class="contact-name">Marcus Hale</p>
      <p class="contact-title">President</p>
      <p class="contact-line">418 6290 3375
        <svg class="contact-icon" viewBox="0 0 16 16" aria-hidden="true"><path d="M4 1 L6.5 4.5 L5 6.5 C6 8.5 7.5 10 9.5 11 L11.5 9.5 L15 12 L13.5 15 C7 14.5 1.5 9 1 2.5 Z" fill="#fff"/></svg>
      </p>
      <p class="contact-line">marcus@halvernmail.com
        <svg class="contact-icon" viewBox="0 0 16 16" aria-hidden="true"><rect x="1" y="3" width="14" height="10" fill="#fff"/><path d="M1 3 L8 9 L15 3" fill="none" stroke="var(--brand-red)" stroke-width="1.4"/></svg>
      </p>
      <p class="contact-line">www.halverninspect.com
        <svg class="contact-icon" viewBox="0 0 16 16" aria-hidden="true"><circle cx="8" cy="8" r="7" fill="none" stroke="#fff" stroke-width="1.4"/><ellipse cx="8" cy="8" rx="3" ry="7" fill="none" stroke="#fff" stroke-width="1.2"/><line x1="1" y1="8" x2="15" y2="8" stroke="#fff" stroke-width="1.2"/></svg>
      </p>
    </div>
  </section>

  <section class="card card-back" aria-label="Card back">
    <p class="back-web">www.halverninspect.com</p>
    <div class="wordmark">
      <span class="wordmark-text">
        <span class="wordmark-name">Halvern</span>
        <span class="wordmark-sub">Inspections</span>
      </span>
    </div>
  </section>

</main>
</body>
</html>
```